Business Card - high end, modern health care

Hey designers!

We need a double sided business card for the boutique, cutting edge physical therapy rehabilitation centre in Sydney's Northern Beaches.

With the most qualified physios in the area The Harbourview Motion Clinic does what other physiotherapy practices do not, we take our time with our patients giving them longer appointments, better physios and therefor faster results!

We guarantee that the service people receive at THMC will be unparalleled.

Hence we need a business card to reflect our modern, boutique, high end service. The final design needs to reflect that we are in a class of our own yet with the feel of beachside retreat.

Below I have attached our logo in both blue on white and white on blue. The exact colour is;
and the font that we have used in our logo is Tex Gyre Aventador.

I like the idea of the blue as the main colour as it is more eye catching and our signage onto the main road will be in this blue and in the interest of consistency across marketing the blue needs to be a part of the design. However I would appreciate a few designs onto a wooden background as this is a visual theme within the fitout of the practice.

The design needs to be of standard size (91x55mm).

Target Market(s)

We target people who have an end outcome in mind and those who have had poor experiences with other providers and ensure that everyone gets the care that they deserve with a premium service that is tailored to the individuals circumstances. As a premium service, the target market is highly educated, business and tech savvy with the additional target market of elderly people who have self funded their retirement and see value in paying for the best ongoing rehabilitation to maintain independence.

Industry/Entity Type

Physical Therapy

Contact Information for Business Card

Name, designation( Titled Musculoskeletal Physiotherapist... there will also be those in the company that have multiple designations ie 5 or 6 words long), phone number, email, facebook, instagram, address

Font styles to use
Sans Serif

Colors

Designer to choose colors to be used in the design.

Requirements
Must have
• Front - The logo as large as possible, blue or wooden theme, and all of the important details.
• Back - A blank space/lines on which to write appointment times (no "Appointment, date, time" etc.)
Nice to have
• facebook url
• logos for facebook and instagram
• Mini logos for the phone and email?

```html
<!DOCTYPE html>
<html lang="en">
<head>
<meta charset="utf-8">
<title>The Harbourview Motion Clinic – Business Card</title>
<link rel="stylesheet" href="https://fonts.googleapis.com/css2?family=Montserrat:wght@500;700&family=Open+Sans:wght@400&display=swap">
<style>
  :root {
    --backdrop: #2b2b2b;
    --brand-blue: #0a55a6;
    --card-white: #ffffff;
    --panel-white: #f4f4f4;
    --ink-grey: #575757;
    --rule-grey: #7a7a7a;
    --faint-blue: #edf1f7;
  }
  html, body {
    margin: 0;
    padding: 0;
    width: 1200px;
    height: 960px;
    overflow: hidden;
    background: var(--backdrop);
  }
  .canvas {
    position: relative;
    width: 1200px;
    height: 960px;
  }
  .card {
    position: absolute;
    width: 598px;
    height: 342px;
    border-radius: 22px;
    overflow: hidden;
  }
  .card-front { left: 322px; top: 108px; background: var(--panel-white); }
  .card-back  { left: 320px; top: 493px; background: var(--card-white); }

  .front-shape { position: absolute; inset: 0; }

  .contact-block {
    position: absolute;
    left: 23px;
    top: 68px;
    color: var(--card-white);
    font-family: "Montserrat", sans-serif;
    font-weight: 500;
    font-size: 14.5px;
    line-height: 19px;
  }
  .person-name { margin: 0; font-weight: 700; font-size: 19px; line-height: 22px; }
  .person-title { margin: 0 0 18px; font-weight: 700; font-size: 14.5px; line-height: 18px; }
  .address { margin: 0 0 10px; }
  .contact-list { list-style: none; margin: 0; padding: 0; }
  .contact-list li { display: flex; align-items: center; height: 19px; }
  .contact-icon { width: 13px; height: 13px; margin-right: 9px; flex: none; }

  .brand-mark {
    position: absolute;
    left: 354px;
    top: 68px;
    width: 160px;
    height: 160px;
    border-radius: 50%;
    background: var(--brand-blue);
  }
  .brand-name {
    position: absolute;
    left: 318px;
    top: 240px;
    width: 232px;
    margin: 0;
    text-align: center;
    color: var(--brand-blue);
    font-family: "Montserrat", sans-serif;
    font-weight: 700;
    font-size: 17px;
    line-height: 21px;
    letter-spacing: 0.5px;
    text-transform: uppercase;
  }

  .back-ring { position: absolute; inset: 0; }
  .appointment-form {
    position: absolute;
    inset: 0;
    font-family: "Open Sans", sans-serif;
    font-size: 15.5px;
    color: var(--ink-grey);
  }
  .field-label { position: absolute; }
  .rule { position: absolute; height: 1px; background: var(--rule-grey); }
</style>
</head>
<body>
<main class="canvas">

  <section class="card card-front" aria-label="Card front">
    <svg class="front-shape" width="598" height="342" viewBox="0 0 598 342" aria-hidden="true">
      <path d="M0 0 H398 A173 173 0 0 0 403 342 H0 Z" fill="var(--brand-blue)"/>
      <path d="M384 0 A180 180 0 0 0 390 342" fill="none" stroke="var(--card-white)" stroke-width="2.5"/>
    </svg>

    <div class="contact-block">
      <h1 class="person-name">DANIEL HART</h1>
      <p class="person-title">CEO/FOUNDER</p>
      <p class="address">42 Seacliff Parade<br>Manly, NSW 2095</p>
      <ul class="contact-list">
        <li>
          <svg class="contact-icon" viewBox="0 0 16 16" aria-hidden="true"><path fill="#fff" d="M3.6 1.2 6 3.6 4.7 5.6c.9 2.2 2.6 3.9 4.8 4.8l2-1.3 2.4 2.4-1.4 2.3C7.1 13.6 2.4 8.9 1.2 2.6Z"/></svg>
          612 905 4417
        </li>
        <li>
          <svg class="contact-icon" viewBox="0 0 16 16" aria-hidden="true"><rect x="1.5" y="3.5" width="13" height="9" fill="#fff"/><path d="M1.5 3.5 8 9l6.5-5.5" fill="none" stroke="var(--brand-blue)" stroke-width="1.3"/></svg>
          dan@hvmotion.com
        </li>
        <li>
          <svg class="contact-icon" viewBox="0 0 16 16" aria-hidden="true"><circle cx="8" cy="8" r="6.5" fill="none" stroke="#fff" stroke-width="1.5"/><path d="M1.5 8h13M8 1.5c-3 3.5-3 9.5 0 13M8 1.5c3 3.5 3 9.5 0 13" fill="none" stroke="#fff" stroke-width="1.2"/></svg>
          www.hvmotion.com
        </li>
        <li>
          <svg class="contact-icon" viewBox="0 0 16 16" aria-hidden="true"><rect x="2" y="2" width="12" height="12" fill="#fff"/></svg>
          /hvmotionclinic
        </li>
        <li>
          <svg class="contact-icon" viewBox="0 0 16 16" aria-hidden="true"><rect x="2" y="2" width="12" height="12" fill="#fff"/></svg>
          @hvmotion
        </li>
      </ul>
    </div>

    <div class="brand-mark" aria-hidden="true"></div>
    <p class="brand-name">The Harbourview<br>Motion Clinic</p>
  </section>

  <section class="card card-back" aria-label="Card back">
    <svg class="back-ring" width="598" height="342" viewBox="0 0 598 342" aria-hidden="true">
      <circle cx="300" cy="178" r="138" fill="none" stroke="var(--faint-blue)" stroke-width="22"/>
    </svg>
    <div class="appointment-form">
      <span class="field-label" style="left:32px; top:40px;">Name</span>
      <div class="rule" style="left:80px; top:56px; width:478px;"></div>

      <span class="field-label" style="left:32px; top:83px;">Date</span>
      <div class="rule" style="left:72px; top:99px; width:261px;"></div>
      <span class="field-label" style="left:340px; top:83px;">Time</span>
      <div class="rule" style="left:383px; top:99px; width:115px;"></div>
      <span class="field-label" style="left:503px; top:83px;">am/pm</span>

      <div class="rule" style="left:35px; top:139px; width:523px;"></div>
      <div class="rule" style="left:35px; top:179px; width:523px;"></div>
      <div class="rule" style="left:35px; top:219px; width:523px;"></div>
      <div class="rule" style="left:35px; top:259px; width:523px;"></div>
      <div class="rule" style="left:35px; top:299px; width:523px;"></div>
    </div>
  </section>

</main>
</body>
</html>
```